Real Estate Acquisition Company Needs Business Card Design

Bellwick Real Estate is in need of a business card design!

As a Real Estate Acquisition Company, Bellwick Real Estate conducts mutually beneficial real estate transactions that actively consider the needs of the seller. At Bellwick Real Estate we’re actively buying properties from those that see value in a direct transaction, but more importantly want reassurances that they, personally, are in integral part of it. Of course, it all starts with fair market value, but it doesn’t stop there. We’ve found the most success when we offer more. And with our deep experience in this industry, we’ve discovered that we have a lot to offer!

We already have a logo and brand guidelines that we've uploaded. Our final design should stay true to the guidelines. We are looking for a business card design that has two names (Ex. Jane Doe & John Doe) and contact information for each person- this way the company principals can share a card as they often do business as a team.
Updates

The criteria was unfortunately not met on most designs. We are looking for a card that has a layout for TWO names and respective contact information for each of the two people. Almost all designs only had a space for one name and one set of contact information.

Industry/Entity Type

Real Estate

Contact Information for Business Card

We are looking for a business card design that has two names (Ex. Jane Doe & John Doe) and each of their contact information- this way the company principals can share a card as they often do business as a team.

Font styles to use
Other font styles liked:
• Use Brand Guidelines

Requirements
Must have
• Please stay true to our Brand Guidelines for colours, fonts, and positioning of logo.

We require a layout for two names and respective contact information. The company principals work as a team and want a card that has both their information on it.

```html
<!DOCTYPE html>
<html lang="en">
<head>
<meta charset="utf-8">
<title>Bellwick Real Estate – Business Card</title>
<link rel="stylesheet" href="https://fonts.googleapis.com/css2?family=Lato:wght@400;700;900&display=swap">
<style>
  :root {
    --backdrop: #aaa09f;
    --navy: #17223a;
    --gold: #f0b548;
    --white: #ffffff;
  }
  * { margin: 0; padding: 0; box-sizing: border-box; }
  html, body {
    width: 1200px;
    height: 800px;
    overflow: hidden;
    background: var(--backdrop);
    font-family: "Lato", Arial, sans-serif;
  }
  .stage { position: relative; width: 1200px; height: 800px; }

  .card {
    position: absolute;
    top: 284px;
    width: 429px;
    height: 238px;
    border-radius: 9px;
    overflow: hidden;
  }
  .card--front { left: 110px; background: var(--navy); }
  .card--back  { left: 638px; background: var(--white); }

  .brand {
    position: absolute;
    display: flex;
    align-items: center;
    gap: 10px;
    white-space: nowrap;
  }
  .brand__dot {
    width: 20px;
    height: 20px;
    border-radius: 50%;
    background: var(--gold);
    flex: none;
  }
  .brand__name {
    font-weight: 900;
    font-size: 25px;
    letter-spacing: 1.5px;
    text-transform: uppercase;
  }
  .card--front .brand { left: 22px; top: 100px; }
  .card--front .brand__name { color: var(--white); }
  .card--back .brand { left: 24px; top: 34px; }
  .card--back .brand__name { color: var(--navy); }

  .team {
    position: absolute;
    left: 24px;
    right: 20px;
    top: 104px;
    display: flex;
    gap: 18px;
  }
  .person {
    flex: 1;
    padding-left: 10px;
    border-left: 1.5px solid var(--gold);
    color: var(--navy);
  }
  .person__name { font-weight: 700; font-size: 16px; line-height: 20px; }
  .person__role {
    font-weight: 400;
    font-size: 11.5px;
    letter-spacing: 1px;
    line-height: 16px;
    margin-bottom: 6px;
  }

  .contacts {
    list-style: none;
    font-size: 11px;
    font-weight: 700;
    letter-spacing: 0.4px;
  }
  .contacts__item {
    display: flex;
    align-items: center;
    height: 16.7px;
    gap: 5px;
    white-space: nowrap;
  }
  .contacts__icon { width: 10px; height: 10px; fill: var(--navy); flex: none; }

  .card__band {
    position: absolute;
    left: 0;
    bottom: 0;
    width: 100%;
    height: 15px;
    background: var(--navy);
  }
</style>
</head>
<body>
<main class="stage">
  <section class="card card--front" aria-label="Card front">
    <div class="brand">
      <span class="brand__dot"></span>
      <span class="brand__name">Bellwick Real Estate</span>
    </div>
  </section>

  <section class="card card--back" aria-label="Card back">
    <div class="brand">
      <span class="brand__dot"></span>
      <span class="brand__name">Bellwick Real Estate</span>
    </div>

    <div class="team">
      <article class="person">
        <p class="person__name">John Doe</p>
        <p class="person__role">CEO</p>
        <ul class="contacts">
          <li class="contacts__item">
            <svg class="contacts__icon" viewBox="0 0 24 24"><path d="M6.6 10.8a15.1 15.1 0 0 0 6.6 6.6l2.2-2.2a1 1 0 0 1 1-.25 11.4 11.4 0 0 0 3.6.57 1 1 0 0 1 1 1V20a1 1 0 0 1-1 1A17 17 0 0 1 3 4a1 1 0 0 1 1-1h3.5a1 1 0 0 1 1 1c0 1.25.2 2.45.57 3.57a1 1 0 0 1-.25 1z"/></svg>
            <span>+00123456789</span>
          </li>
          <li class="contacts__item">
            <svg class="contacts__icon" viewBox="0 0 24 24"><path d="M2 5h20v14H2z M3.5 6.5 12 13l8.5-6.5" fill="var(--navy)" stroke="var(--white)" stroke-width="1.5"/></svg>
            <span>john@mail.com</span>
          </li>
          <li class="contacts__item">
            <svg class="contacts__icon" viewBox="0 0 24 24"><circle cx="12" cy="12" r="10"/><path d="M7 6c2 1 1 3 3 4s0 4 2 5M15 4c-1 2 1 3 3 3M14 20c0-2 2-3 4-3" stroke="var(--white)" stroke-width="1.6" fill="none"/></svg>
            <span>www.yourwebsite.com</span>
          </li>
        </ul>
      </article>

      <article class="person">
        <p class="person__name">Jane Doe</p>
        <p class="person__role">COO</p>
        <ul class="contacts">
          <li class="contacts__item">
            <svg class="contacts__icon" viewBox="0 0 24 24"><path d="M6.6 10.8a15.1 15.1 0 0 0 6.6 6.6l2.2-2.2a1 1 0 0 1 1-.25 11.4 11.4 0 0 0 3.6.57 1 1 0 0 1 1 1V20a1 1 0 0 1-1 1A17 17 0 0 1 3 4a1 1 0 0 1 1-1h3.5a1 1 0 0 1 1 1c0 1.25.2 2.45.57 3.57a1 1 0 0 1-.25 1z"/></svg>
            <span>+00987654321</span>
          </li>
          <li class="contacts__item">
            <svg class="contacts__icon" viewBox="0 0 24 24"><path d="M2 5h20v14H2z M3.5 6.5 12 13l8.5-6.5" fill="var(--navy)" stroke="var(--white)" stroke-width="1.5"/></svg>
            <span>jane@mail.com</span>
          </li>
          <li class="contacts__item">
            <svg class="contacts__icon" viewBox="0 0 24 24"><circle cx="12" cy="12" r="10"/><path d="M7 6c2 1 1 3 3 4s0 4 2 5M15 4c-1 2 1 3 3 3M14 20c0-2 2-3 4-3" stroke="var(--white)" stroke-width="1.6" fill="none"/></svg>
            <span>www.yourwebsite.com</span>
          </li>
        </ul>
      </article>
    </div>

    <div class="card__band"></div>
  </section>
</main>
</body>
</html>
```